New Company Logo & Responsive Website Design for Codeworks Heron

Codeworks Heron provides a white labeled, digital lending platform technology solutions to the mortgage industry via a SaaS model. Our target market is Mortgage Companies and Banks who are looking for innovative technology to assist both borrowers and loan originators with the lending process, while automating as much of he process as possible.

Codeworks Heron is our company name, and our modular software offerings Include the following Products:

1) Applicant Heron: A customizable, web based, point-of-sale application for borrowers to complete a loan application, and guide them through the mortgage process.

POS Definition
"A point of sale (POS) is the client-facing software solution that allows borrowers to create a customer portal, apply for a loan online, and seamlessly submit needed documentation."

2) Ledger Heron: A Mortgage Loan Origination System

LOS Definition
"A Mortgage Loan Origination System (LOS) is a platform that takes a completed loan application and facilitates the mortgage transaction from origination to post closing. LOS systems may include document management, pricing and eligibility engines, and compliance tools to decrease risk and increase loan manufacturing quality.

3) Dwelling Heron: A brandable, home search website

The LOS and POS definitions provided above are just for your understanding of what these products are, not to be included word-for-word as website content.

We are looking for designs that are elegant, convey technical competency, simple to navigate, and set us apart from the competition.

We are not set on any particular colors at this point, so feel free to choose the best colors for your particular designs.

Please include company logo, both desktop and mobile designs with a template design for the website sub pages.

Some Examples of Mortgage Technology Websites offering similar products. These are to show the typical content, not designs that we particularly like or dislike.

https://brantiq.example/
https://www.clearvantro.example/
https://www.abodefundbuddy.example/
https://www.debtquokka.example/
https://www.ternixapps.example/products/trail

Please send comments with additional questions.

Thank You For your participation.

Mortgage Companies

```html
<!DOCTYPE html>
<html lang="en">
<head>
<meta charset="utf-8">
<title>Codeworks Heron — Mortgage Fintech Startup</title>
<link rel="stylesheet" href="https://fonts.googleapis.com/css2?family=Montserrat:wght@700;800&family=Roboto:ital,wght@0,400;0,500;0,700;1,400&display=swap">
<style>
:root{
  --blue:#2563c9;
  --blue-deep:#1d52b3;
  --red:#e8173f;
  --sky:#d6e6f8;
  --ink:#161a22;
  --text:#3c4250;
  --muted:#8a909b;
  --line:#d9dde3;
  --footer:#1c1c1e;
  --white:#ffffff;
  --tint:#dbe5f5;
}
*{margin:0;padding:0;box-sizing:border-box}
html,body{width:1200px;height:4539px;overflow:hidden}
body{position:relative;background:var(--white);font-family:'Roboto',Arial,sans-serif;color:var(--text)}
.abs{position:absolute}
.heading{font-family:'Montserrat',Arial,sans-serif;font-weight:800;color:var(--ink);text-align:center;font-size:44px;letter-spacing:.5px;text-transform:uppercase}
.dash{position:absolute;width:30px;height:4px;background:var(--red)}
.btn{position:absolute;display:flex;align-items:center;justify-content:center;background:var(--red);color:var(--white);font-family:'Roboto',Arial,sans-serif;font-weight:700;font-size:12px;text-transform:uppercase;border-radius:20px;height:36px;text-decoration:none}
.dots{position:absolute;background:var(--tint);opacity:.55;border-radius:4px}

/* header */
.site-header{position:absolute;left:0;top:0;width:1200px;height:85px;background:var(--white)}
.brand{position:absolute;left:144px;top:20px;font-family:'Roboto',Arial,sans-serif;font-weight:700;font-size:38px;color:var(--ink);letter-spacing:-.5px}
.nav{position:absolute;top:36px;font-size:14px;color:#444}
.nav-bar{position:absolute;left:490px;top:34px;width:3px;height:22px;background:var(--red)}
.btn-login{background:var(--blue);left:814px;top:26px;width:84px}

/* hero */
.hero-title{position:absolute;left:0;top:150px;width:1200px;text-align:center;color:var(--white);font-family:'Montserrat',Arial,sans-serif;font-weight:800;font-size:45px}
.hero-text{position:absolute;left:220px;top:220px;width:760px;text-align:center;color:var(--white);font-size:14.5px;line-height:23px}
.hero-media{position:absolute;left:222px;top:368px;width:758px;height:386px;background:linear-gradient(120deg,#6f6a62 0%,#cfc7bb 45%,#e8e3dc 70%,#8f8578 100%)}
.play{position:absolute;left:562px;top:523px;width:76px;height:76px}

/* offers */
.offer{position:absolute;top:976px;width:290px;height:328px;background:var(--white);border-radius:14px;box-shadow:0 6px 26px rgba(30,50,90,.16);text-align:center;padding:0 32px}
.offer.active{border:2px solid var(--red)}
.offer h3{font-family:'Roboto',Arial,sans-serif;font-weight:500;font-size:23px;color:var(--blue);margin-top:8px}
.offer .lead{font-weight:500;font-size:11px;color:var(--ink);line-height:19px;margin-top:10px}
.offer p{font-size:11px;line-height:19px;color:var(--text);margin-top:8px}
.offer .icon{margin-top:20px}
.offer-photo{width:272px;height:226px;margin:10px auto 0;background:linear-gradient(160deg,#7fb2b8 0%,#3f6f6e 45%,#1c2f2c 100%);border-radius:2px}

/* about */
.about-photo{position:absolute;left:601px;top:1425px;width:599px;height:672px;background:linear-gradient(135deg,#4e4b48 0%,#8b857d 40%,#d8d4cd 70%,#5d5a57 100%)}
.about-panel{position:absolute;left:0;top:1494px;width:689px;height:532px;background:var(--white)}
.about-title{position:absolute;left:144px;top:1578px;font-family:'Montserrat',Arial,sans-serif;font-weight:800;font-size:44px;color:var(--ink)}
.about-text{position:absolute;left:144px;top:1651px;width:494px;font-size:12.4px;line-height:24.8px;color:var(--text)}

/* partners */
.partners{position:absolute;left:160px;top:2318px;width:880px;display:flex;justify-content:space-between;align-items:center}
.partner{font-family:'Roboto',Arial,sans-serif;font-weight:700;font-size:17px;color:#9aa1ab}
.partner-badge{width:36px;height:36px;background:#9aa1ab;border-radius:2px}
.pager{position:absolute;top:2397px;width:7px;height:7px;border-radius:50%;background:#9aa1ab}

/* news */
.news-card{position:absolute;top:2724px;width:280px;height:364px;background:var(--white);border:1px solid #c8d2df}
.news-card.active{border:2px solid var(--red)}
.news-photo{position:absolute;left:13px;top:12px;width:252px;height:170px}
.date{position:absolute;left:20px;top:198px;width:48px;height:46px;background:var(--red);color:var(--white);text-align:center;font-weight:700;line-height:1}
.date b{display:block;font-size:20px;margin-top:5px}
.date span{font-size:13px;font-weight:500}
.news-card h4{position:absolute;left:80px;top:198px;width:186px;font-size:15px;font-weight:500;color:var(--ink);line-height:22px}
.news-card p{position:absolute;left:20px;top:256px;width:240px;font-size:11px;line-height:19px;color:var(--muted)}
.news-card a{position:absolute;left:20px;top:326px;font-size:12px;font-weight:700;color:var(--blue);text-decoration:none}

/* reviews */
.review-bg{position:absolute;left:0;top:3330px;width:1200px;height:700px;background:radial-gradient(ellipse at 55% 45%,#f3ece4 0%,#f8f5f1 50%,#ffffff 85%)}
.quote-mark{position:absolute;left:570px;top:3570px;font-family:'Montserrat',Arial,sans-serif;font-style:italic;font-weight:800;font-size:60px;color:#c9c9c9}
.quote{position:absolute;left:230px;top:3622px;width:740px;text-align:center;font-style:italic;font-size:20px;line-height:34px;color:#555}
.reviewer{position:absolute;left:0;top:3748px;width:1200px;text-align:center;font-weight:500;font-size:20px;color:var(--blue)}
.stars{color:#f2b705;letter-spacing:2px;margin-left:12px}

/* cta */
.cta-title{position:absolute;left:0;top:4100px;width:1200px;text-align:center;font-family:'Montserrat',Arial,sans-serif;font-weight:800;font-size:44px;color:var(--white)}
.cta-text{position:absolute;left:300px;top:4180px;width:600px;text-align:center;color:var(--white);font-size:19px;line-height:26px}

/* footer */
.site-footer{position:absolute;left:0;top:4345px;width:1200px;height:194px;background:var(--footer);color:var(--white)}
.social{position:absolute;top:32px;width:40px;height:40px;border-radius:50%;background:var(--white)}
.footer-ask{position:absolute;left:553px;top:42px;font-size:18px}
.footer-nav{position:absolute;top:140px;font-size:14px;font-weight:500}
.legal{position:absolute;left:692px;top:142px;font-size:11px;color:#ddd}
</style>
</head>
<body>

<!-- hero backdrop -->
<svg class="abs" style="left:0;top:0" width="1200" height="560" aria-hidden="true">
  <polygon points="0,85 1200,85 1200,316 980,370 222,500 0,456" fill="#2563c9"/>
</svg>
<div class="abs" role="img" aria-label="Faint photo of a house in the hero background" style="left:0;top:85px;width:260px;height:370px;background:linear-gradient(180deg,rgba(255,255,255,.06),rgba(255,255,255,0))"></div>

<header class="site-header">
  <div class="brand">Codeworks Heron</div>
  <div class="nav-bar"></div>
  <nav>
    <span class="nav" style="left:502px">Products</span>
    <span class="nav" style="left:603px">Solutions</span>
    <span class="nav" style="left:706px">Resources</span>
  </nav>
  <a class="btn btn-login" href="#">Login</a>
  <a class="btn" href="#" style="left:904px;top:26px;width:150px">Request a demo</a>
</header>

<h1 class="hero-title">MORTGAGE FINTECH STARTUP</h1>
<p class="hero-text">Lorem ipsum dolor sit amet, consectetur adipiscing elit, sed do eiusmod tempor incididunt ut labore et dolore magna aliquum suspendisse ultrices gravidommodo viverra maecenas accumsan lacus vel facilisis.</p>
<a class="btn" href="#" style="left:524px;top:289px;width:152px">Request a demo</a>

<div class="dots" role="img" aria-label="Dot grid accent" style="left:104px;top:500px;width:110px;height:92px"></div>
<div class="dots" role="img" aria-label="Dot grid accent" style="left:990px;top:645px;width:52px;height:118px"></div>
<div class="dots" role="img" aria-label="Dot grid accent" style="left:872px;top:762px;width:170px;height:52px"></div>

<div class="hero-media" role="img" aria-label="Video still of a smiling couple looking at a laptop at home"></div>
<svg class="play" viewBox="0 0 76 76" aria-label="Play video" role="img">
  <circle cx="38" cy="38" r="38" fill="#e8173f"/>
  <polygon points="29,22 29,54 55,38" fill="#fff"/>
</svg>

<!-- what we offer -->
<div class="dash" style="left:585px;top:863px"></div>
<h2 class="heading abs" style="left:0;top:884px;width:1200px">What we offer</h2>

<article class="offer" style="left:144px">
  <svg class="icon" width="64" height="56" viewBox="0 0 64 56" aria-hidden="true" fill="none" stroke="#e8173f" stroke-width="2">
    <path d="M16 26 L32 12 L48 26 M20 23 V44 H44 V23"/><rect x="28" y="32" width="8" height="12"/><path d="M6 46 Q18 40 26 46 H40 M8 10 l4 4 M56 10 l-4 4 M32 2 v6"/>
  </svg>
  <h3>Applicant Heron</h3>
  <p class="lead">A customizable, web based, point-of-sale application for borrowers to complete a loan application, and guide them through the mortgage process.</p>
  <p>A point of sale (POS) is the client-facing software solution that allows borrowers to create a customer portal, apply for a loan online, and seamlessly submit needed documentation.</p>
</article>

<article class="offer active" style="left:455px;width:290px;padding:0 8px">
  <div class="offer-photo" role="img" aria-label="Photo of a small model house beside stacks of coins with percent signs"></div>
  <h3 style="margin-top:12px">Dwelling Heron</h3>
  <p class="lead" style="margin-top:6px">A brandable, home search website</p>
</article>
<div class="dots" role="img" aria-label="Dot grid accent" style="left:446px;top:1250px;width:68px;height:70px;background:#f3b3c1"></div>

<article class="offer" style="left:766px">
  <svg class="icon" width="64" height="56" viewBox="0 0 64 56" aria-hidden="true" fill="none" stroke="#e8173f" stroke-width="2">
    <rect x="18" y="4" width="26" height="36"/><path d="M23 12 H39 M23 18 H39 M23 24 H34"/><path d="M12 48 L26 36 L40 48 M16 45 V54 H36 V45"/><circle cx="46" cy="44" r="7"/>
  </svg>
  <h3>Ledger Heron</h3>
  <p class="lead">A Mortgage Loan Origination System</p>
  <p>A Mortgage Loan Origination System (LOS) is a platform that takes a completed loan application and facilitates the mortgage transaction from origination to post closing. LOS systems may include document management, pricing and eligibility engines, and compliance tools to decrease risk and increase loan manufacturing quality.</p>
</article>

<!-- about -->
<div class="dots" role="img" aria-label="Dot grid accent" style="left:12px;top:1436px;width:170px;height:170px"></div>
<div class="about-photo" role="img" aria-label="Photo of a couple reviewing mortgage paperwork at a desk with an advisor"></div>
<div class="about-panel"></div>
<div class="dots" role="img" aria-label="Dot grid accent" style="left:1022px;top:2034px;width:176px;height:52px;background:#fff;opacity:.8"></div>
<div class="dash" style="left:144px;top:1557px"></div>
<h2 class="about-title">ABOUT US</h2>
<p class="about-text">Lorem ipsum dolor sit amet, consectetur adipiscing elit, sed do eempor incididunt ut labore et dolore magna aliqua. Quis ipsum suspendisse ultrices gravida. Risus commodo viverra maecenas accumsan lacus vel facilisiLorem ipsum dolor sitectetur adipiscing elit, sed do eiusmod tempor incididunt ut labore et dolore magna aliqua. Quis ipsum suspendisse ultrices grisus commodo viverra maecenas accumsan lacus vel facilisis. Lorem ipsum dolor sit amet, consectetur adipiscing elit, sed do eiusmod tempor incididunt ut labore et dolore magna aliqua. Quis ipsum suspendisse ultrices gravida. Risus commodo viverra maecenas accumsan lacus vel facilisis. Lorem ipsum dolor sit amet, consectetur adipiscing elit, sed do eiusmod tempor incididunt ut labore et dolore magna aliqua. Quis ipsum suspendisse ultrices gravida.</p>
<a class="btn" href="#" style="left:144px;top:1927px;width:152px">Read more</a>

<!-- partners -->
<div class="dash" style="left:585px;top:2195px"></div>
<h2 class="heading abs" style="left:0;top:2216px;width:1200px">Partners</h2>
<div class="partners">
  <span class="partner">LedgerWeekly</span>
  <span class="partner">Market Herald</span>
  <span class="partner-badge" role="img" aria-label="Partner badge"></span>
  <span class="partner">Dailytips</span>
  <span class="partner">Fortis Review</span>
  <span class="partner">Lakeside Courier</span>
  <span class="partner">NewsPost</span>
</div>
<span class="pager" style="left:564px"></span>
<span class="pager" style="left:596px;background:var(--blue)"></span>
<span class="pager" style="left:628px"></span>
<div class="dots" role="img" aria-label="Dot grid accent" style="left:8px;top:2434px;width:150px;height:68px"></div>

<!-- news -->
<svg class="abs" style="left:0;top:2511px" width="1200" height="850" aria-hidden="true">
  <path d="M0,0 H1200 V690 Q900,640 700,720 Q480,810 380,830 Q200,860 0,730 Z" fill="#d6e6f8"/>
</svg>
<div class="dash" style="left:585px;top:2607px"></div>
<h2 class="heading abs" style="left:0;top:2628px;width:1200px">From the news</h2>

<article class="news-card" style="left:155px">
  <div class="news-photo" role="img" aria-label="Photo of hands signing documents beside a model house" style="background:linear-gradient(135deg,#6d7e8c,#c4ccd2 55%,#3c4852)"></div>
  <div class="date"><b>02</b><span>JAN</span></div>
  <h4>Pellentesque faucibus Ut accumsan ultric</h4>
  <p>Duis quam Nam eget lacus Aliquam erat volutpat Quisque dignissim congue leovel lacus vitae felis vestibulum</p>
  <a href="#">READ MORE</a>
</article>
<article class="news-card active" style="left:462px">
  <div class="news-photo" role="img" aria-label="Photo of a family relaxing on a sofa among moving boxes" style="background:linear-gradient(180deg,#e9e6e1,#b9a58f 60%,#8c7965)"></div>
  <div class="date"><b>02</b><span>JAN</span></div>
  <h4>Pellentesque faucibus Ut accumsan ultric</h4>
  <p>Duis quam Nam eget lacus Aliquam erat volutpat Quisque dignissim congue leovel lacus vitae felis vestibulum</p>
  <a href="#">READ MORE</a>
</article>
<div class="dots" role="img" aria-label="Dot grid accent" style="left:668px;top:3096px;width:70px;height:24px;background:#f3b3c1"></div>
<article class="news-card" style="left:766px">
  <div class="news-photo" role="img" aria-label="Photo of a tablet showing a mortgage application next to a coffee cup" style="background:linear-gradient(135deg,#3b3d40,#8e8e8c 50%,#d5d3cf)"></div>
  <div class="date"><b>02</b><span>JAN</span></div>
  <h4>Pellentesque faucibus Ut accumsan ultric</h4>
  <p>Duis quam Nam eget lacus Aliquam erat volutpat Quisque dignissim congue leovel lacus vitae felis vestibulum</p>
  <a href="#">READ MORE</a>
</article>
<a class="btn" href="#" style="left:524px;top:3139px;width:152px">Load more</a>
<div class="dots" role="img" aria-label="Dot grid accent" style="left:1030px;top:3110px;width:170px;height:112px;background:#b9cdeb"></div>

<!-- reviews -->
<div class="review-bg" role="img" aria-label="Faded photo of a happy family at home among moving boxes"></div>
<div class="dash" style="left:585px;top:3439px"></div>
<h2 class="heading abs" style="left:0;top:3460px;width:1200px">Customer reviews</h2>
<div class="quote-mark">//</div>
<p class="quote">“Lorem ipsum dolor sit amet, consectetur adipiscing elit, sed do eiusmod tempor incididunt ut labore et dolore magna aliqua. Quis ipsum suspendisse ultrices commodo viverra maecenas accumsan lacus vel facilisis”</p>
<svg class="abs" style="left:122px;top:3636px" width="34" height="66" aria-label="Previous review" role="img"><polyline points="32,2 2,33 32,64" fill="none" stroke="#999" stroke-width="1.5"/></svg>
<svg class="abs" style="left:1044px;top:3636px" width="34" height="66" aria-label="Next review" role="img"><polyline points="2,2 32,33 2,64" fill="none" stroke="#999" stroke-width="1.5"/></svg>
<div class="reviewer">Nora Whitfield <span class="stars">★★★★★</span></div>
<a class="btn" href="#" style="left:524px;top:3821px;width:152px">More reviews</a>

<!-- call to action -->
<svg class="abs" style="left:0;top:3900px" width="1200" height="446" aria-hidden="true">
  <path d="M0,175 Q300,150 560,90 Q820,20 920,60 Q1080,110 1200,105 V446 H0 Z" fill="#2563c9"/>
</svg>
<div class="dots" role="img" aria-label="Dot grid accent" style="left:990px;top:3880px;width:170px;height:92px;background:#b9cdeb"></div>
<div class="dots" role="img" aria-label="Dot grid accent" style="left:0;top:4072px;width:168px;height:70px;background:#b9cdeb"></div>
<div class="dash" style="left:585px;top:4081px"></div>
<h2 class="cta-title">READY TO SEE MORE?</h2>
<p class="cta-text">Lorem ipsum dolor sit amet, consectetur adipiscingdo eiusmod tempor incididunt ut labore et dolore magna aliqua.</p>
<a class="btn" href="#" style="left:524px;top:4264px;width:152px">Get started</a>

<!-- footer -->
<footer class="site-footer">
  <span class="social" role="img" aria-label="Social profile" style="left:144px"></span>
  <span class="social" role="img" aria-label="Social profile" style="left:195px"></span>
  <span class="social" role="img" aria-label="Social profile" style="left:246px"></span>
  <span class="footer-ask">ARE YOU READY TO GET STARTED?</span>
  <a class="btn" href="#" style="left:902px;top:32px;width:152px">Sign up for free</a>
  <span class="footer-nav" style="left:144px">PRODUCTS</span>
  <span class="footer-nav" style="left:273px">SOLUTIONS</span>
  <span class="footer-nav" style="left:406px">RESOURCES</span>
  <span class="legal">© 2022 Codeworks Heron, All Rights Reserved &nbsp;|&nbsp; Privacy &nbsp;|&nbsp; Terms of Use</span>
</footer>

</body>
</html>
```